Group training gym/bootcamp needs a web design

We need a website for our gym that is based in Sydney. We have indoor functional training classes and outdoor bootcamp classes. We would like the web site to have a video (to be created) and photo gallery. I would like the site made on word press and i would like to be able to make minor changes such as changing images and text without having to use a designer.

The website should have the following pages: home page; the gym; the bootcamp; photo gallery; about us; contact.

I have uploaded our logo and i would like to keep to these colour (blue,yellow,silver) and black is also allowed

Target Market(s)

18-50 male and female

Industry/Entity Type

Gym

Coding

Coded - Design and coding required

Number of Pages Required

5+ page

Font styles to use
Sans Serif

Colors
0692cd
fbed22
1b1b1b
e8e8e8

Requirements
Must have
• The website should have the following pages: home page; the gym; the bootcamp; photo gallery; about us; contact.
• I have uploaded our logo and i would like to keep to these colour (blue,yellow,silver) and black is also allowed
• Video upload and photo upload

```html
<!DOCTYPE html>
<html lang="en">
<head>
<meta charset="utf-8">
<title>Forge Motion Gym</title>
<link href="https://fonts.googleapis.com/css2?family=Roboto:ital,wght@0,400;0,500;0,700;0,900;1,900&display=swap" rel="stylesheet">
<style>
:root{
  --blue:#4a97cf;
  --blue-deep:#0692cd;
  --yellow:#fbed22;
  --ink:#1b1b1b;
  --silver:#e8e8e8;
  --navy:#221c35;
  --white:#ffffff;
  --muted:#9a9a9a;
  --footer:#050505;
}
*{margin:0;padding:0;box-sizing:border-box}
html,body{width:1200px;height:3303px;overflow:hidden}
body{font-family:'Roboto',Arial,sans-serif;color:var(--ink);background:var(--white);position:relative}
.abs{position:absolute}
.btn{position:absolute;display:flex;align-items:center;justify-content:center;font-size:13px;font-weight:500;text-transform:uppercase;letter-spacing:.3px;z-index:2}
.btn-yellow{background:var(--yellow);color:var(--ink)}
.btn-blue{background:var(--blue);color:var(--white)}
.photo{position:absolute;z-index:0}

/* header */
.site-header{position:absolute;left:0;top:0;width:1200px;height:110px;background:var(--navy)}
.brand{position:absolute;left:88px;top:36px;display:flex;align-items:center;gap:10px;color:var(--yellow);font-weight:900;font-size:17px;text-transform:uppercase;letter-spacing:.5px}
.brand-mark{width:30px;height:30px;border-radius:50%;background:var(--blue-deep)}
.main-nav{position:absolute;left:465px;top:44px;display:flex;gap:24px;font-size:12px;font-weight:500;color:var(--white);text-transform:uppercase}
.main-nav .current{color:var(--yellow)}
.join{left:1017px;top:35px;width:96px;height:36px}

/* hero */
.hero{left:0;top:110px;width:1200px;height:496px;background:linear-gradient(110deg,#d9d4d0 0%,#8a7a78 35%,#4d4850 60%,#cfc9c4 100%)}
.hero-kicker{left:650px;top:262px;color:var(--white);font-size:31px;font-weight:400;text-transform:uppercase}
.hero-title{left:650px;top:305px;color:var(--white);font-size:72px;font-weight:900;font-style:italic;text-transform:uppercase;letter-spacing:-1px}
.hero-btn{left:650px;top:407px;width:150px;height:44px;font-size:17px}
.slider-dots{left:1150px;top:315px}

/* welcome */
.welcome{left:0;top:606px;width:1200px;height:539px;background:linear-gradient(90deg,#ffffff 0%,#f6f6f6 60%,#fbfbfb 100%)}
.welcome-kicker{left:88px;top:686px;font-size:22px;font-weight:400;color:#333;z-index:2}
.section-title{font-weight:700;font-size:31px;color:#222;z-index:2}
.welcome-title{left:86px;top:718px}
.rule{position:absolute;height:2px;background:var(--blue);z-index:2}
.body-copy{position:absolute;font-size:11.5px;line-height:24px;text-align:justify;z-index:2}
.welcome-copy{left:88px;top:796px;width:546px;color:var(--muted)}
.welcome-btn{left:88px;top:958px;width:115px;height:36px}
.welcome-photo{left:660px;top:683px;width:400px;height:407px;background:radial-gradient(ellipse at 55% 50%,#d89aa8 0%,#e8d8d6 35%,#f6f6f6 70%)}

/* indoor */
.indoor-photo{left:0;top:1145px;width:548px;height:485px;background:linear-gradient(135deg,#cfc6bb 0%,#a79c90 45%,#7f6a78 75%,#d9d2ca 100%)}
.indoor{left:548px;top:1145px;width:652px;height:485px;background:var(--blue)}
.indoor-title{left:599px;top:1214px;color:var(--white)}
.indoor-copy{left:599px;top:1280px;width:487px;color:var(--white)}
.indoor-btn{left:599px;top:1515px;width:117px;height:37px}

/* outdoor */
.outdoor{left:0;top:1630px;width:650px;height:484px;background:var(--yellow)}
.outdoor-title{left:84px;top:1699px;color:var(--ink)}
.outdoor-copy{left:86px;top:1758px;width:488px;color:var(--ink)}
.outdoor-btn{left:88px;top:2000px;width:114px;height:37px}
.outdoor-photo{left:650px;top:1630px;width:550px;height:484px;background:linear-gradient(180deg,#a9c3d8 0%,#b8b1a4 30%,#a08a6c 55%,#7f8f4a 100%)}

/* gallery */
.gallery-title{left:0;top:2182px;width:1200px;text-align:center;font-size:31px;font-weight:700;color:#222}
.gallery-rule{left:552px;top:2230px;width:96px}
.g1{left:0;top:2275px;width:288px;height:213px;background:linear-gradient(135deg,#8a7d72,#c9c0b5 50%,#5e5a5e)}
.g2{left:304px;top:2275px;width:288px;height:213px;background:linear-gradient(135deg,#4f4b4a,#a29788 50%,#6c6260)}
.g3{left:608px;top:2275px;width:286px;height:213px;background:linear-gradient(135deg,#9aa270,#c88a6c 50%,#6f8a3e)}
.g4{left:909px;top:2275px;width:291px;height:213px;background:linear-gradient(135deg,#5f7e3c,#9fb074 50%,#4b6a2c)}

/* video */
.video{left:0;top:2499px;width:1200px;height:441px;background:linear-gradient(180deg,#8f8780 0%,#6d6a68 50%,#4c4c50 100%)}
.video-title{left:0;top:2650px;width:1200px;text-align:center;color:var(--white);font-size:44px;font-weight:500;text-transform:uppercase;letter-spacing:.5px;z-index:2}
.play{left:573px;top:2722px;z-index:2}

/* footer */
.site-footer{left:0;top:2940px;width:1200px;height:363px;background:var(--footer)}
.footer-brand{left:88px;top:3050px;display:flex;align-items:center;gap:12px;color:var(--yellow);font-weight:900;font-size:22px;text-transform:uppercase;letter-spacing:.5px}
.footer-brand .brand-mark{width:40px;height:40px}
.footer-head{position:absolute;top:2998px;color:var(--white);font-size:18px;font-weight:400;text-transform:uppercase}
.email-field{left:436px;top:3045px;width:207px;height:44px;background:#2b2b2d;color:#7c7c7c;font-size:12px;padding:14px 0 0 28px}
.subscribe{left:436px;top:3109px;width:207px;height:44px;font-size:16px}
.contact-line{position:absolute;left:718px;color:var(--white);font-size:11px;line-height:17px;display:flex;gap:20px}
.contact-line svg{flex:none;margin-top:2px}
.sitemap{position:absolute;left:1020px;top:3041px;list-style:none;color:var(--white);font-size:11px;line-height:23.5px}
.footer-rule{left:0;top:3226px;width:1200px;height:1px;background:#2a2a2a}
.copyright{left:324px;top:3260px;color:#bdbdbd;font-size:11.5px}
.socials{left:736px;top:3259px;display:flex;gap:14px;align-items:center}
.socials .sep{width:1px;height:16px;background:#888;margin-right:6px}
.socials .dot{width:12px;height:12px;border-radius:50%;background:#d6d6d6}
</style>
</head>
<body>

<header class="site-header">
  <div class="brand"><span class="brand-mark"></span>Forge Motion</div>
  <nav class="main-nav">
    <span class="current">Home</span><span>The Gym</span><span>The Bootcamp</span><span>Photo Gallery</span><span>About Us</span><span>Contact Us</span>
  </nav>
  <div class="btn btn-yellow join">Join Now</div>
</header>

<section>
  <div class="photo hero" role="img" aria-label="Woman doing a push-up in a gym"></div>
  <div class="abs hero-kicker">Keep a health body.</div>
  <div class="abs hero-title">Get fit now!</div>
  <div class="btn btn-yellow hero-btn">Learn More</div>
  <svg class="abs slider-dots" width="22" height="90" viewBox="0 0 22 90">
    <circle cx="11" cy="11" r="9" fill="none" stroke="#dddddd" stroke-width="2"/>
    <circle cx="11" cy="42" r="9" fill="none" stroke="#fbed22" stroke-width="2"/>
    <circle cx="11" cy="42" r="5" fill="#fbed22"/>
    <circle cx="11" cy="73" r="9" fill="none" stroke="#dddddd" stroke-width="2"/>
  </svg>
</section>

<section>
  <div class="abs welcome"></div>
  <div class="photo welcome-photo" role="img" aria-label="Woman in a pink top doing a side lunge stretch"></div>
  <div class="abs welcome-kicker">Welcome to</div>
  <h1 class="abs section-title welcome-title">Forge Motion Gym</h1>
  <div class="rule" style="left:88px;top:765px;width:485px"></div>
  <p class="body-copy welcome-copy">Lorem Ipsum is simply dummy text of the printing and typesetting industry. Lorem Ipsum has been the industry's standard dummy text ever since the 1500s, when an unknown printer took a galley of type and scrambled it to make a type specimen book. It has survived not only five centuries, but also the leap into electronic typesetting, remaining essentially unchanged. It was popularised in the 1960s with the release of Letraset sheets containing Lorem Ipsum passages, and more recently with desktop publishing software...</p>
  <div class="btn btn-blue welcome-btn">Learn More</div>
</section>

<section>
  <div class="photo indoor-photo" role="img" aria-label="Trainer helping a woman with sit-ups indoors"></div>
  <div class="abs indoor"></div>
  <h2 class="abs section-title indoor-title">Indoor Functional Classes</h2>
  <div class="rule" style="left:599px;top:1261px;width:487px;background:#ffffff"></div>
  <p class="body-copy indoor-copy">Lorem Ipsum is simply dummy text of the printing and typesetting industry. Lorem Ipsum has been the industry's standard dummy text ever since the 1500s, when an unknown printer took a galley of type and scrambled it to make a type specimen book. It has survived not only five centuries, but also the leap into electronic typesetting, remaining essentially unchanged. It was popularised in the 1960s with the release of Letraset sheets containing Lorem Ipsum passages, and more recently with desktop publishing software like Aldus PageMaker including versions of Lorem Ipsum.Lorem Ipsum is simply dummy text of the printing and typesetting industry. Lorem Ipsum has been the industry's standard dummy text ever since the 1500s,...</p>
  <div class="btn btn-yellow indoor-btn">Learn More</div>
</section>

<section>
  <div class="abs outdoor"></div>
  <h2 class="abs section-title outdoor-title">Outdoor Bootcamp Classes</h2>
  <p class="body-copy outdoor-copy">Lorem Ipsum is simply dummy text of the printing and typesetting industry. Lorem Ipsum has been the industry's standard dummy text ever since the 1500s, when an unknown printer took a galley of type and scrambled it to make a type specimen book. It has survived not only five centuries, but also the leap into electronic typesetting, remaining essentially unchanged. It was popularised in the 1960s with the release of Letraset sheets containing Lorem Ipsum passages, and more recently with desktop publishing software like Aldus PageMaker including versions of Lorem Ipsum.Lorem Ipsum is simply dummy text of the printing and typesetting industry. Lorem Ipsum has been the industry's standard dummy text ever since the 1500s,...</p>
  <div class="btn btn-blue outdoor-btn">Learn More</div>
  <div class="photo outdoor-photo" role="img" aria-label="Group doing push-ups on mats outdoors in a park"></div>
</section>

<section>
  <h2 class="abs gallery-title">Gallery</h2>
  <div class="rule gallery-rule"></div>
  <div class="photo g1" role="img" aria-label="Indoor class lifting kettlebells"></div>
  <div class="photo g2" role="img" aria-label="Group training session in a studio"></div>
  <div class="photo g3" role="img" aria-label="Bootcamp group planking on mats"></div>
  <div class="photo g4" role="img" aria-label="Outdoor group doing lunges on grass"></div>
</section>

<section>
  <div class="photo video" role="img" aria-label="Video still of a woman in an athletic lunge"></div>
  <div class="abs video-title">Forge Motion Gym</div>
  <svg class="abs play" width="52" height="52" viewBox="0 0 52 52" aria-label="Play video">
    <circle cx="26" cy="26" r="26" fill="#ffffff"/>
    <circle cx="26" cy="26" r="20" fill="#3a3a3a"/>
    <path d="M22 18 L34 26 L22 34 Z" fill="#ffffff"/>
  </svg>
</section>

<footer>
  <div class="abs site-footer"></div>
  <div class="abs footer-brand"><span class="brand-mark"></span>Forge Motion</div>

  <div class="footer-head" style="left:436px">Newsletter</div>
  <div class="abs email-field">Your Email</div>
  <div class="btn btn-yellow subscribe">Subscribe</div>

  <div class="footer-head" style="left:718px">Contact Us</div>
  <div class="contact-line" style="top:3042px">
    <svg width="10" height="12" viewBox="0 0 10 12"><path d="M5 0a4 4 0 0 1 4 4c0 3-4 8-4 8S1 7 1 4a4 4 0 0 1 4-4z" fill="#fff"/><circle cx="5" cy="4" r="1.5" fill="#050505"/></svg>
    <span>42 Harbour Row, Surry Hills,<br>Sydney, 2010</span>
  </div>
  <div class="contact-line" style="top:3094px">
    <svg width="10" height="12" viewBox="0 0 10 12"><path d="M2 0h2l1 3-1.5 1a7 7 0 0 0 3 3L8 5.5l2 1V9c0 1-1 2-2 2C4 11 0 7 0 2 0 1 1 0 2 0z" fill="#fff"/></svg>
    <span>555-010-2468</span>
  </div>
  <div class="contact-line" style="top:3127px">
    <svg width="11" height="12" viewBox="0 0 11 12"><rect x="0" y="2" width="11" height="8" fill="#fff"/><path d="M0 2l5.5 4L11 2" fill="none" stroke="#050505" stroke-width="1"/></svg>
    <span>hello@forgemotion.example</span>
  </div>

  <div class="footer-head" style="left:1020px">Sitemap</div>
  <ul class="sitemap">
    <li>&gt; Home</li><li>&gt; The Gym</li><li>&gt; The Bootcamp</li><li>&gt; Photo Gallery</li><li>&gt; About us</li><li>&gt; Contact us</li>
  </ul>

  <div class="abs footer-rule"></div>
  <div class="abs copyright">Copyright © 2017. Forge Motion Gym. All Rights Reserved.</div>
  <div class="abs socials">
    <span class="sep"></span><span class="dot"></span><span class="dot"></span><span class="dot"></span><span class="dot"></span><span class="dot"></span>
  </div>
</footer>

</body>
</html>
```